Steadfast Corner Vending Needs a Promotional Flyer

Design a one page, one sided 8 1/2" x 11" flyer that can be handed out to potential customers. Please keep printing efficiencies in mind. See attached old flyers and company website (steadfastcornervend.example) for reference of services. I have also attached our current logo.

```html
<!DOCTYPE html>
<html lang="en">
<head>
<meta charset="utf-8">
<title>Steadfast Corner Vending – Flyer</title>
<link href="https://fonts.googleapis.com/css2?family=Poppins:wght@400;500;600;700;800&display=swap" rel="stylesheet">
<style>
:root{
  --navy:#0f2a3a;
  --blue:#1a9ad6;
  --white:#ffffff;
  --ink:#0f2a3a;
  --photo-dark:#3b4048;
  --photo-red:#c8352a;
  --coffee:#6b4a2e;
  --wood:#7a5636;
}
*{margin:0;padding:0;box-sizing:border-box}
html,body{width:834px;height:1200px;overflow:hidden;background:var(--white)}
body{font-family:'Poppins',sans-serif;color:var(--ink);position:relative}
.abs{position:absolute}

.hero-blue{left:492px;top:0;width:342px;height:468px;background:var(--blue)}
.hero-navy{left:700px;top:0;width:134px;height:468px;background:var(--navy)}
.machines{left:449px;top:146px;width:348px;height:316px;border-radius:4px;
  background:linear-gradient(90deg,var(--photo-dark) 0 44%,var(--photo-red) 44% 100%)}
.badge{left:548px;top:38px;width:102px;height:102px;border-radius:50%;background:var(--navy);
  display:flex;align-items:center;justify-content:center}
.badge-inner{width:80px;height:80px;border-radius:50%;background:var(--white);text-align:center;
  display:flex;flex-direction:column;justify-content:center;line-height:1}
.badge-num{font-weight:800;font-size:24px;color:var(--navy)}
.badge-word{font-weight:700;font-size:12px;color:var(--blue)}
.badge-sub{font-weight:600;font-size:6.5px;letter-spacing:.5px;color:var(--navy);margin-top:2px}

.brand{left:72px;top:80px}
.brand-welcome{font-weight:800;font-size:20px;color:var(--blue)}
.brand-name{display:flex;align-items:center;gap:8px;margin-top:4px;font-weight:800;font-size:26px;color:var(--navy);line-height:1.1}
.brand-name .mark{width:18px;height:18px;background:var(--blue)}

.headline{left:70px;top:228px;line-height:1;font-weight:800}
.headline .dark{font-size:40px;color:var(--navy);display:block;margin-bottom:4px}
.headline .big{font-size:58px;color:var(--blue);display:block;margin-top:2px}

.why{left:48px;top:505px;width:738px;height:188px;background:var(--navy);color:var(--white)}
.why-title{position:absolute;left:22px;top:10px;font-size:19px;font-weight:400}
.why-title b{color:var(--blue);font-weight:700}
.why-item{position:absolute;display:flex;gap:10px;font-size:10.6px;line-height:1.3;font-weight:400}
.why-item svg{flex:none;width:22px;height:22px}

.section-head{left:69px;top:704px;font-size:27px;font-weight:800;color:var(--navy)}
.tag{background:var(--blue);color:var(--white);font-weight:800;font-size:17px;line-height:1;padding:3px 6px;text-transform:uppercase}
.bullets{list-style:none;font-size:10.4px;font-weight:600;line-height:1.2}
.bullets li{position:relative;padding-left:12px;margin-bottom:1.5px}
.bullets li::before{content:"";position:absolute;left:0;top:4px;width:6px;height:6px;border-radius:50%;background:var(--blue)}
.ticks{display:grid;font-size:10px;font-weight:400;line-height:1.25;padding-left:12px}
.ticks span{white-space:nowrap}
.ticks span::before{content:"✓ ";font-size:9px}
.photo{border:1.5px solid var(--navy)}

.footer{left:0;top:1110px;width:834px;height:90px}
.call{left:76px;top:1117px;color:var(--white)}
.call-label{font-size:17px;font-weight:600;letter-spacing:.5px}
.call-number{font-size:27px;font-weight:700;display:flex;align-items:center;gap:6px;line-height:1.1}
.contact{display:flex;gap:8px;font-size:12px;line-height:1.3;color:var(--navy)}
</style>
</head>
<body>

<div class="abs hero-blue"></div>
<div class="abs hero-navy"></div>
<div class="abs machines" role="img" aria-label="Photo of a snack vending machine beside a cold drink vending machine"></div>
<div class="abs badge"><div class="badge-inner"><span class="badge-num">30+</span><span class="badge-word">YEAR</span><span class="badge-sub">EXPERIENCE</span></div></div>

<div class="abs brand">
  <div class="brand-welcome">WELCOME TO</div>
  <div class="brand-name"><span class="mark"></span><span>STEADFAST CORNER<br>VENDING</span></div>
</div>

<h1 class="abs headline">
  <span class="dark">WELCOME</span>
  <span class="dark">TO STEADFAST</span>
  <span class="big">CORNER</span>
  <span class="big">VENDING</span>
</h1>

<section class="abs why">
  <h2 class="why-title">Why Choose Our <b>Vending Machine Services?</b></h2>
  <div class="why-item" style="left:22px;top:46px;width:230px"><svg viewBox="0 0 22 22"><circle cx="11" cy="11" r="10" fill="none" stroke="var(--blue)" stroke-width="1.5"/><circle cx="11" cy="11" r="7" fill="var(--blue)"/><path d="M12 6l-4 6h3l-1 4 4-6h-3z" fill="var(--white)"/></svg><span>Our warehouse is just minutes away so we can get there quickly if a problem should arise.</span></div>
  <div class="why-item" style="left:22px;top:110px;width:230px"><svg viewBox="0 0 22 22"><circle cx="11" cy="11" r="10" fill="none" stroke="var(--blue)" stroke-width="1.5"/><circle cx="11" cy="11" r="7" fill="var(--blue)"/><rect x="8" y="7" width="6" height="8" fill="none" stroke="var(--white)"/></svg><span>We are a small company<br>that is BIG on service.</span></div>
  <div class="why-item" style="left:22px;top:156px;width:260px"><svg viewBox="0 0 22 22"><circle cx="11" cy="11" r="10" fill="none" stroke="var(--blue)" stroke-width="1.5"/><circle cx="11" cy="11" r="7" fill="var(--blue)"/><circle cx="9" cy="9" r="1.6" fill="var(--white)"/><circle cx="13" cy="9" r="1.6" fill="var(--white)"/><path d="M6.5 15c0-3 5-3 5 0M10.5 15c0-3 5-3 5 0" fill="var(--white)"/></svg><span>Customer Service is our priority.</span></div>
  <div class="why-item" style="left:274px;top:46px;width:190px"><svg viewBox="0 0 22 22"><circle cx="11" cy="11" r="10" fill="none" stroke="var(--blue)" stroke-width="1.5"/><circle cx="11" cy="11" r="7" fill="var(--blue)"/><path d="M8 10l3-2 3 2v4H8z" fill="var(--white)"/></svg><span>We are Owner-Operators so we truly CARE about our customers.</span></div>
  <div class="why-item" style="left:274px;top:110px;width:190px"><svg viewBox="0 0 22 22"><circle cx="11" cy="11" r="10" fill="none" stroke="var(--blue)" stroke-width="1.5"/><circle cx="11" cy="11" r="7" fill="var(--blue)"/><circle cx="11" cy="10" r="2.5" fill="none" stroke="var(--white)"/><path d="M9.5 12.5l-1 3M12.5 12.5l1 3" stroke="var(--white)"/></svg><span>We are also trained to fix many problems on the spot.</span></div>
  <div class="why-item" style="left:494px;top:46px;width:220px"><svg viewBox="0 0 22 22"><circle cx="11" cy="11" r="10" fill="none" stroke="var(--blue)" stroke-width="1.5"/><circle cx="11" cy="11" r="7" fill="var(--blue)"/><path d="M7 13h8M9 10h4" stroke="var(--white)" stroke-width="1.4"/></svg><span>We will supply machines<br>to your facility.</span></div>
  <div class="why-item" style="left:494px;top:94px;width:230px"><svg viewBox="0 0 22 22"><circle cx="11" cy="11" r="10" fill="none" stroke="var(--blue)" stroke-width="1.5"/><circle cx="11" cy="11" r="7" fill="var(--blue)"/><rect x="7.5" y="8" width="7" height="7" fill="none" stroke="var(--white)"/></svg><span>Your employees can choose what types of snacks and drinks they would like to see in the machines.</span></div>
</section>

<h2 class="abs section-head">STEADFAST SUPERIOR SERVICE</h2>

<!-- Vending machine services -->
<div class="abs tag" style="left:70px;top:768px;width:185px">Vending Machine<br>Services</div>
<div class="abs photo" role="img" aria-label="Photo of bottled drinks inside a vending machine" style="left:263px;top:768px;width:129px;height:108px;background:linear-gradient(180deg,#c9d2da,#8a9aa8 50%,#b0413a)"></div>
<ul class="abs bullets" style="left:71px;top:811px">
  <li>Discover Reliability,</li><li>Variety At Zero Cost to You</li><li>Convenience</li><li>Quality</li>
</ul>

<!-- Coffee service -->
<div class="abs tag" style="left:70px;top:876px;width:175px">Coffee Service</div>
<div class="abs photo" role="img" aria-label="Photo of a cup of coffee on a saucer with coffee beans" style="left:263px;top:878px;width:129px;height:106px;background:radial-gradient(circle at 55% 45%,#f4efe9 0 22%,var(--coffee) 40%,#2e1d12)"></div>
<ul class="abs bullets" style="left:71px;top:902px"><li>Reliability</li><li>Our Coffee Selection</li></ul>
<div class="abs ticks" style="left:71px;top:932px;grid-template-columns:98px 80px">
  <span>Harborline</span><span>Ridgecup</span><span>Morning Mill</span><span>Copperleaf</span><span>North Pine</span><span>Bramwell</span><span>Oakridge Roast</span>
</div>
<ul class="abs bullets" style="left:71px;top:1001px"><li>Tea and other Tasty Hot Beverages</li><li>Coffee Accessories</li></ul>
<div class="abs ticks" style="left:71px;top:1031px;grid-template-columns:99px 92px 120px">
  <span>Coffee Pots</span><span>Sleeves</span><span>Dulcera</span>
  <span>Filters</span><span>Napkins</span><span>Liquid Creamers</span>
  <span>Cups</span><span>Sugar</span><span>flavored and regular</span>
  <span>Stirrers</span><span>Lite-Sweet</span>
</div>

<!-- Pantry service -->
<div class="abs tag" style="left:435px;top:767px;width:183px">Pantry Service</div>
<div class="abs photo" role="img" aria-label="Photo of an office pantry with wooden shelves and a drink cooler" style="left:634px;top:767px;width:130px;height:107px;background:linear-gradient(90deg,var(--wood) 0 68%,#cfd8de 68%)"></div>
<ul class="abs bullets" style="left:436px;top:792px;width:188px">
  <li>A Snack Time Oasis in Your Workspace</li><li>Tailored to Your Tastes</li><li>Healthy Choices, Happy Teams</li><li>Seamless Restocking and Management</li><li>Flexible and Hassle-Free</li><li>Enhancing Workplace Culture</li>
</ul>

<!-- Micro-market -->
<div class="abs tag" style="left:435px;top:917px;width:183px">Micro-Market</div>
<div class="abs photo" role="img" aria-label="Photo of micro-market shelves stocked with snacks" style="left:634px;top:917px;width:130px;height:106px;background:linear-gradient(90deg,#5a4030,#c98a4a 50%,#3a5c8a)"></div>
<ul class="abs bullets" style="left:436px;top:941px;width:188px">
  <li>Experience Unmatched Convenience</li><li>Tailored to Your Taste</li><li>Seamless and Secure Transactions</li><li>Freshness Guaranteed</li><li>Smart Inventory Management</li><li>Promoting Workplace Wellbeing</li>
</ul>

<!-- Footer -->
<svg class="abs footer" viewBox="0 0 834 90" aria-hidden="true">
  <polygon points="0,0 316,0 345,90 0,90" fill="var(--navy)"/>
  <polygon points="316,0 322,0 352,86 834,86 834,90 345,90" fill="var(--blue)"/>
</svg>
<div class="abs call">
  <div class="call-label">CALL US AT</div>
  <div class="call-number"><svg width="16" height="16" viewBox="0 0 24 24"><path d="M6 2l4 4-2 3c1 3 4 6 7 7l3-2 4 4-3 4C10 22 2 14 2 5z" fill="var(--blue)"/></svg>630-555-0148</div>
</div>
<div class="abs contact" style="left:366px;top:1140px">
  <svg width="14" height="18" viewBox="0 0 14 18"><path d="M7 1a6 6 0 0 1 6 6c0 4-6 10-6 10S1 11 1 7a6 6 0 0 1 6-6z" fill="none" stroke="var(--blue)" stroke-width="1.6"/><circle cx="7" cy="7" r="2" fill="var(--blue)"/></svg>
  <span>4180 Harlow Ave, Unit 12,<br>Maple Bend, IL 60599</span>
</div>
<div class="abs contact" style="left:590px;top:1140px">
  <svg width="16" height="16" viewBox="0 0 16 16"><circle cx="8" cy="8" r="7" fill="none" stroke="var(--blue)" stroke-width="1.5"/><path d="M1 8h14M8 1c-3 4-3 10 0 14M8 1c3 4 3 10 0 14" fill="none" stroke="var(--blue)"/></svg>
  <span style="font-size:11.5px">steadfastcornervend.example</span>
</div>

</body>
</html>
```